Business Card- Can you make it cool vs boring!

Need a refresh on my business card! Want it to be modern but simple, classic and a pop of coolness! we do senior living and it is boring. but that doesn't mean our business card have to look boring! Open to two sided cards. our website is www.Dunmere-PK.com

Target Market(s)

capital market

Industry/Entity Type

senior housing/ real estate

Contact Information for Business Card

logo/ name/ cell/ address/ www.Dunmere-PK.com/ space for a QR code

Requirements
Must have
• maybe a QR code (do not make prominent I may not use the QR so design where it can be taken out) that link to more about us/ landing page. needs to be modern but clean
Should not have
• clip art or script

```html
<!DOCTYPE html>
<html lang="en">
<head>
<meta charset="utf-8">
<title>Dunmere Park – Business Card</title>
<link href="https://fonts.googleapis.com/css2?family=Lato:wght@400;700;900&display=swap" rel="stylesheet">
<style>
  :root {
    --rust: #b0532a;
    --rust-deep: #9c4622;
    --paper: #ffffff;
    --ink: #1c1c1c;
    --backdrop: #1e1e1e;
    --divider: rgba(255,255,255,0.45);
  }
  * { box-sizing: border-box; margin: 0; padding: 0; }
  html, body {
    width: 1200px; height: 1015px; overflow: hidden;
    background: var(--backdrop);
    font-family: "Lato", sans-serif;
  }
  .canvas { position: relative; width: 1200px; height: 1015px; }

  .card {
    position: absolute; left: 280px;
    width: 640px; height: 366px;
    overflow: hidden;
    box-shadow: 0 10px 30px rgba(0,0,0,0.55);
  }

  /* Back side */
  .card-back { top: 90px; background: var(--rust); }
  .card-back .pattern {
    position: absolute; inset: 0;
    background: linear-gradient(135deg, var(--rust) 0%, var(--rust-deep) 100%);
  }
  .card-back .brand-name {
    position: absolute; right: 40px; bottom: 44px;
    color: var(--paper); font-weight: 700; font-size: 30px;
  }

  /* Front side */
  .card-front { top: 540px; background: var(--paper); }
  .card-front .brand-name {
    position: absolute; top: 52px; right: 70px;
    color: var(--rust); font-weight: 700; font-size: 58px; letter-spacing: 1px;
  }
  .info-band {
    position: absolute; left: 0; right: 0; top: 176px; height: 124px;
    background: var(--rust);
    display: flex; align-items: center;
  }
  .person {
    width: 330px; text-align: right; padding-right: 26px;
    color: var(--paper);
  }
  .person .name { font-weight: 900; font-size: 22px; letter-spacing: 0.5px; }
  .person .title { font-weight: 400; font-size: 17px; margin-top: 2px; }
  .band-divider { width: 1px; height: 78px; background: var(--divider); }
  .contacts { list-style: none; padding-left: 24px; color: var(--paper); font-size: 17px; }
  .contacts li { display: flex; align-items: center; gap: 10px; line-height: 27px; }
  .contacts svg { width: 16px; height: 16px; fill: none; stroke: var(--paper); stroke-width: 1.6; }
  .address {
    position: absolute; left: 0; right: 0; bottom: 20px;
    text-align: center; color: var(--ink); font-size: 17px;
  }
</style>
</head>
<body>
<main class="canvas">

  <section class="card card-back" aria-label="Card back">
    <div class="pattern" role="img" aria-label="Repeating embossed monogram pattern in rust tones"></div>
    <span class="brand-name">Dunmere Park</span>
  </section>

  <section class="card card-front" aria-label="Card front">
    <span class="brand-name">Dunmere Park</span>

    <div class="info-band">
      <div class="person">
        <div class="name">MARCUS ELLERY</div>
        <div class="title">Managing Director</div>
      </div>
      <div class="band-divider"></div>
      <ul class="contacts">
        <li>
          <svg viewBox="0 0 16 16"><path d="M3 1.5l3 3-1.5 2a8 8 0 0 0 5 5l2-1.5 3 3-2 2C7 14.5 1.5 9 1 3z"/></svg>
          044-987 654 321
        </li>
        <li>
          <svg viewBox="0 0 16 16"><rect x="1" y="3" width="14" height="10"/><path d="M1 3l7 6 7-6"/></svg>
          info@dunmere-pk.com
        </li>
        <li>
          <svg viewBox="0 0 16 16"><circle cx="8" cy="8" r="7"/><ellipse cx="8" cy="8" rx="3" ry="7"/><path d="M1 8h14M2.5 4.5h11M2.5 11.5h11"/></svg>
          www.Dunmere-PK.com
        </li>
      </ul>
    </div>

    <p class="address">18, Willow Court Lane, Northfield, 20418</p>
  </section>

</main>
</body>
</html>
```